Veranix - Solution provider in business consulting

Veranix is a swiss based company providing solutions for developing markets. The business covers various fields of business consulting, such as supply chain, product costs, quality management and manufacturing management. The Business operates in a efficient, straight and solution oriented manner.
The final design should communicate these characteristics. Asian people as well as as western people shall identify the qualities of the company at first sight.
The customer needs business cards with a simple view but an recognizable design, printed in high quality. Engraved elements such as the globe or simple words are possible.
Available colors are: (RAL)
102/102/102
51/102/102
153/204/153
255/102/51
Font: Calibri

```html
<!DOCTYPE html>
<html lang="en">
<head>
<meta charset="utf-8">
<title>Veranix business card</title>
<link href="https://fonts.googleapis.com/css2?family=Carlito:wght@400;700&display=swap" rel="stylesheet">
<style>
  :root {
    --page-bg: #d9d6d1;
    --card-top: #222222;
    --card-bottom: #050505;
    --ink: #ffffff;
    --ink-soft: #e6e6e6;
    --globe-tint: rgba(255, 255, 255, 0.06);
    --rule: rgba(255, 255, 255, 0.55);
  }
  html, body {
    margin: 0;
    width: 1200px;
    height: 1022px;
    overflow: hidden;
    background: var(--page-bg);
  }
  .business-card {
    position: absolute;
    left: 120px;
    top: 201px;
    width: 960px;
    height: 620px;
    border-radius: 30px;
    overflow: hidden;
    background: linear-gradient(160deg, var(--card-top) 0%, #111111 45%, var(--card-bottom) 100%);
    box-shadow: 0 18px 40px rgba(0, 0, 0, 0.35);
    font-family: "Carlito", "Calibri", sans-serif;
    color: var(--ink);
  }
  .globe-decoration {
    position: absolute;
    left: 420px;
    top: -40px;
    width: 700px;
    height: 700px;
  }
  .brand-name {
    position: absolute;
    left: 70px;
    top: 360px;
    display: flex;
    align-items: center;
    gap: 22px;
    font-size: 128px;
    font-weight: 400;
    line-height: 1;
    letter-spacing: 1px;
  }
  .brand-dot {
    width: 92px;
    height: 92px;
    border-radius: 50%;
    background: var(--ink);
  }
  .contact-block {
    position: absolute;
    left: 560px;
    top: 118px;
    padding-left: 26px;
    border-left: 2px solid var(--rule);
  }
  .person-name {
    margin: 0;
    font-size: 36px;
    font-weight: 700;
    line-height: 1.1;
  }
  .person-role {
    margin: 4px 0 18px;
    font-size: 22px;
    color: var(--ink-soft);
  }
  .company-address {
    margin: 0 0 16px;
    font-size: 22px;
    line-height: 1.3;
    color: var(--ink-soft);
    font-style: normal;
  }
  .contact-list {
    list-style: none;
    margin: 0;
    padding: 0;
    font-size: 22px;
    line-height: 1.35;
    color: var(--ink-soft);
  }
  .contact-list li {
    display: flex;
    align-items: center;
    gap: 12px;
  }
  .contact-icon {
    width: 16px;
    height: 16px;
    flex: none;
  }
</style>
</head>
<body>
  <div class="business-card">
    <svg class="globe-decoration" viewBox="0 0 700 700" role="img" aria-label="Faint globe decoration">
      <circle cx="350" cy="350" r="345" fill="var(--globe-tint)"/>
    </svg>

    <div class="brand-name">
      <span>Veranix</span>
      <span class="brand-dot" aria-hidden="true"></span>
    </div>

    <div class="contact-block">
      <h1 class="person-name">Marco Feller</h1>
      <p class="person-role">CEO</p>
      <address class="company-address">
        Veranix GmbH Lindenweg 14<br>
        8400 Winterthur Switzerland
      </address>
      <ul class="contact-list">
        <li>
          <svg class="contact-icon" viewBox="0 0 16 16" aria-hidden="true"><rect x="4" y="1" width="8" height="14" rx="1.5" fill="none" stroke="#fff" stroke-width="1.6"/><circle cx="8" cy="12.5" r="0.9" fill="#fff"/></svg>
          +41 79 555 0182
        </li>
        <li>
          <svg class="contact-icon" viewBox="0 0 16 16" aria-hidden="true"><path d="M3 2 L6 2 L7 5 L5.5 6.5 C6.5 8.5 7.5 9.5 9.5 10.5 L11 9 L14 10 L14 13 C14 13.6 13.6 14 13 14 C7 14 2 9 2 3 C2 2.4 2.4 2 3 2 Z" fill="#fff"/></svg>
          +41 71 555 0147
        </li>
        <li>
          <svg class="contact-icon" viewBox="0 0 16 16" aria-hidden="true"><rect x="1.5" y="3.5" width="13" height="9" fill="none" stroke="#fff" stroke-width="1.4"/><path d="M1.5 3.5 L8 9 L14.5 3.5" fill="none" stroke="#fff" stroke-width="1.4"/></svg>
          marco.feller@veranix.ch
        </li>
        <li>
          <svg class="contact-icon" viewBox="0 0 16 16" aria-hidden="true"><circle cx="8" cy="8" r="6.5" fill="none" stroke="#fff" stroke-width="1.4"/><ellipse cx="8" cy="8" rx="2.8" ry="6.5" fill="none" stroke="#fff" stroke-width="1.1"/><line x1="1.5" y1="8" x2="14.5" y2="8" stroke="#fff" stroke-width="1.1"/></svg>
          www.veranix.ch
        </li>
      </ul>
    </div>
  </div>
</body>
</html>
```